Business Card, A4 Letter Head and DL Envelope for Brandvelle

We are looking for a design for our Business Card, A4 Letter Head and DL Envelope.

Brandvelle is a distributor of promotional products. We specialize in a range of branded promotional products, these include pens, polo shirts, key rings, drink bottles, uniforms and bags to name a few. We are experts in marketing and assist companies in choosing the right promotional product for their needs. We will predominately be an online business where customers visit our website and browse our range of promotional products and branding options.

Our colours are black, red, white and grey.

Files must be supplied in eps, pdf and ai format.

Please display the following information:
Derek Halloway
Account Manager
Suite xxx, 212 Ferrow Lane Melbourne, Victoria 3000
Phone +61 3 5550 1827
Mobile +61 455 016 342
sales@brandvelle-example.com.au
www.brandvelle-example.com.au

```html
<!DOCTYPE html>
<html lang="en">
<head>
<meta charset="utf-8">
<title>Brandvelle Stationery</title>
<link href="https://fonts.googleapis.com/css2?family=Open+Sans:wght@400;600;700&family=Dancing+Script:wght@600&display=swap" rel="stylesheet">
<style>
  :root{
    --red:#c8161d;
    --red-deep:#7e0d10;
    --red-bright:#e0242a;
    --black:#0d0d0d;
    --grey:#8a8a8a;
    --grey-light:#d9d9d9;
    --white:#ffffff;
    --ink:#333333;
    --stage:#e9e6e2;
  }
  *{margin:0;padding:0;box-sizing:border-box}
  html,body{width:1200px;height:1024px;overflow:hidden}
  body{background:var(--stage);font-family:"Open Sans",Arial,sans-serif;color:var(--ink);position:relative}
  .item{position:absolute;overflow:hidden;box-shadow:0 2px 6px rgba(0,0,0,.25)}
  .swoosh{position:absolute;left:0;bottom:0;width:100%}

  /* logo lockup */
  .logo{display:flex;flex-direction:column;align-items:center;gap:6px}
  .logo__dot{width:34px;height:34px;border-radius:50%;background:var(--red)}
  .logo__name{font-weight:700;font-size:15px;letter-spacing:.5px;text-transform:uppercase;line-height:1}
  .logo--dark .logo__name{color:var(--ink)}
  .logo--light .logo__name{color:var(--white)}

  /* letterhead */
  .letterhead{left:32px;top:30px;width:343px;height:484px;background:var(--white)}
  .letterhead .logo{position:absolute;left:18px;top:22px}
  .contact{font-size:6.5px;line-height:1.45;color:var(--ink)}
  .contact .tel{color:var(--red)}
  .letterhead .contact{position:absolute;left:212px;top:24px;border-left:1px solid var(--grey-light);padding-left:6px}
  .letter{position:absolute;left:20px;top:154px;width:300px;font-size:6px;line-height:1.5;color:#555}
  .letter__greeting{font-size:8px;color:var(--ink);margin-bottom:8px}
  .letter p{margin-bottom:7px}
  .signature{position:absolute;left:20px;top:386px}
  .signature__name{font-family:"Dancing Script",cursive;font-size:12px;color:var(--ink)}
  .signature__role{font-size:6px;color:#555}
  .web{position:absolute;font-size:8px;color:var(--white)}
  .letterhead .web{right:18px;bottom:10px}

  /* covers */
  .cover{top:30px;width:346px;height:484px}
  .cover--red{left:418px;background:radial-gradient(ellipse at 55% 45%,var(--red-bright),var(--red) 45%,var(--red-deep))}
  .cover--black{left:808px;width:344px;background:radial-gradient(ellipse at 55% 45%,#3a3a3a,#1a1a1a 50%,var(--black))}
  .cover .logo{position:absolute;left:0;right:0;top:42px}
  .cover .logo__dot{width:56px;height:56px}
  .cover .logo__name{font-size:24px}
  .cover--red .logo__dot{background:var(--white)}
  .cover .web{left:0;right:0;bottom:16px;text-align:center;font-size:10px;color:#f2dede}

  /* business cards */
  .card{top:544px;height:174px;border-radius:14px}
  .card--white{left:56px;width:288px;background:var(--white)}
  .card--white .logo{position:absolute;left:22px;top:22px}
  .card__name{position:absolute;left:18px;top:133px;color:var(--white);font-size:9px;line-height:1.3}
  .card__name b{font-weight:400;text-transform:uppercase;font-size:9.5px}
  .card--white .contact{position:absolute;left:172px;top:112px;color:var(--white);font-size:7px}
  .card--white .contact .tel{color:var(--white)}
  .card--white .web{left:18px;bottom:10px;font-size:8px}
  .card--black{left:433px;width:318px;background:linear-gradient(90deg,var(--black),#2a2a2a 60%,#111)}
  .card--red{left:827px;width:307px;background:radial-gradient(ellipse at 70% 40%,var(--red-bright),var(--red) 50%,var(--red-deep))}
  .card__brand{position:absolute;left:18px;top:128px;color:var(--white)}
  .card__brand .logo__name{font-size:15px}
  .card__brand .web{position:static;display:block;margin-top:3px;font-size:7.5px}
  .card__mark{position:absolute;right:34px;top:28px;width:110px;height:110px;border-radius:50%}
  .card--black .card__mark{background:var(--red)}
  .card--red .card__mark{background:var(--white)}

  /* envelopes */
  .envelope{top:744px;height:252px}
  .envelope--front{left:14px;width:367px;background:var(--white)}
  .envelope--front .logo{position:absolute;left:22px;top:24px}
  .envelope--front .contact{position:absolute;left:242px;top:28px;font-size:6.5px}
  .envelope__window{position:absolute;left:18px;top:122px;width:130px;height:44px;border:1px solid #c9c9c9;border-radius:6px;background:linear-gradient(180deg,#f4f4f4,#e6e6e6)}
  .envelope--front .web{right:14px;bottom:8px;font-size:7.5px}
  .envelope--back-white{left:403px;width:374px;background:var(--white)}
  .envelope--back-red{left:799px;width:374px;background:radial-gradient(ellipse at 55% 55%,var(--red),var(--red-deep))}
  .flap{position:absolute;left:0;top:0;width:100%;height:70px}
  .envelope .flap-logo{position:absolute;left:0;right:0;top:10px}
  .flap-logo .logo__dot{width:22px;height:22px}
  .flap-logo .logo__name{font-size:9px;color:var(--white)}
  .envelope--back-red .logo__dot{background:var(--white)}
  .envelope--back-white .logo__dot{background:var(--white)}
  .envelope--back-white .web{left:0;right:0;bottom:10px;text-align:center;color:var(--red);font-size:7.5px}
  .envelope--back-red .web{left:0;right:0;bottom:10px;text-align:center;color:#f2dede;font-size:7.5px}
</style>
</head>
<body>

<!-- A4 letterhead -->
<section class="item letterhead" aria-label="Letterhead">
  <div class="logo logo--dark"><span class="logo__dot"></span><span class="logo__name">Brandvelle</span></div>
  <div class="contact">
    <div class="tel">&#9742; +61 3 5550 1827</div>
    <div class="tel">&#9743; +61 455 016 342</div>
    <div>&#9993; sales@brandvelle-example.com.au</div>
    <div style="margin-top:6px">Suite xxx, 212 Ferrow Lane</div>
    <div>Melbourne, Victoria 3000</div>
  </div>
  <div class="letter">
    <div class="letter__greeting">Lorem Ipsum,</div>
    <p>We thank you for choosing our team to supply your branded goods and we look forward to working with you.</p>
    <p>Our range covers pens, polo shirts, key rings, drink bottles, uniforms and bags, each printed to match your brand colours.</p>
    <p>Our advisers will help you choose the right product for every event, budget and audience, from first sample to delivery.</p>
    <p>Browse our full catalogue online at any time, compare branding options side by side and place your order in minutes.</p>
    <p>Please contact us with any questions about pricing, artwork or delivery times and we will reply within one business day.</p>
  </div>
  <div class="signature">
    <div class="signature__name">Yours Name</div>
    <div class="signature__role">Company Director</div>
  </div>
  <svg class="swoosh" viewBox="0 0 343 80" height="80" preserveAspectRatio="none" aria-hidden="true">
    <path d="M0 34 C120 30 240 20 343 0 L343 20 C240 36 120 44 0 46 Z" fill="#9a9a9a"/>
    <path d="M0 40 C120 36 240 26 343 8 L343 14 C240 32 120 42 0 44 Z" fill="#2a2a2a"/>
    <path d="M0 46 C120 44 240 36 343 20 L343 80 L0 80 Z" fill="var(--red)"/>
  </svg>
  <div class="web">www.brandvelle-example.com.au</div>
</section>

<!-- Presentation folder covers -->
<section class="item cover cover--red" aria-label="Folder cover, red">
  <div class="logo logo--light"><span class="logo__dot"></span><span class="logo__name">Brandvelle</span></div>
  <div class="web">www.brandvelle-example.com.au</div>
</section>

<section class="item cover cover--black" aria-label="Folder cover, black">
  <div class="logo logo--light"><span class="logo__dot"></span><span class="logo__name">Brandvelle</span></div>
  <div class="web">www.brandvelle-example.com.au</div>
</section>

<!-- Business cards -->
<section class="item card card--white" aria-label="Business card front">
  <svg class="swoosh" viewBox="0 0 288 110" height="110" preserveAspectRatio="none" aria-hidden="true">
    <path d="M0 26 C100 10 200 8 288 18 L288 30 C200 22 100 26 0 42 Z" fill="#9a9a9a"/>
    <path d="M0 34 C100 20 200 18 288 26 L288 30 C200 24 100 30 0 42 Z" fill="#2a2a2a"/>
    <path d="M0 42 C100 28 200 24 288 30 L288 110 L0 110 Z" fill="var(--red)"/>
  </svg>
  <div class="logo logo--dark"><span class="logo__dot"></span><span class="logo__name">Brandvelle</span></div>
  <div class="card__name"><b>Derek Halloway</b><br>Account Manager</div>
  <div class="contact">
    <div class="tel">&#9742; +61 3 5550 1827</div>
    <div class="tel">&#9743; +61 455 016 342</div>
    <div>&#9993; sales@brandvelle-example.com.au</div>
    <div style="margin-top:3px">Suite xxx, 212 Ferrow Lane</div>
    <div>Melbourne, Victoria 3000</div>
  </div>
  <div class="web">www.brandvelle-example.com.au</div>
</section>

<section class="item card card--black" aria-label="Business card back, black">
  <span class="card__mark"></span>
  <div class="card__brand"><span class="logo__name">Brandvelle</span><span class="web">www.brandvelle-example.com.au</span></div>
</section>

<section class="item card card--red" aria-label="Business card back, red">
  <span class="card__mark"></span>
  <div class="card__brand"><span class="logo__name">Brandvelle</span><span class="web">www.brandvelle-example.com.au</span></div>
</section>

<!-- DL envelopes -->
<section class="item envelope envelope--front" aria-label="DL envelope front">
  <div class="logo logo--dark"><span class="logo__dot"></span><span class="logo__name">Brandvelle</span></div>
  <div class="contact">
    <div class="tel">&#9742; +61 3 5550 1827</div>
    <div class="tel">&#9743; +61 455 016 342</div>
    <div>&#9993; sales@brandvelle-example.com.au</div>
    <div>Suite xxx, 212 Ferrow Lane</div>
    <div>Melbourne, Victoria 3000</div>
  </div>
  <div class="envelope__window"></div>
  <svg class="swoosh" viewBox="0 0 367 60" height="60" preserveAspectRatio="none" aria-hidden="true">
    <path d="M0 20 C130 22 260 18 367 2 L367 14 C260 28 130 32 0 30 Z" fill="#9a9a9a"/>
    <path d="M0 26 C130 28 260 22 367 8 L367 14 C260 28 130 32 0 30 Z" fill="#2a2a2a"/>
    <path d="M0 30 C130 32 260 28 367 14 L367 60 L0 60 Z" fill="var(--red)"/>
  </svg>
  <div class="web">www.brandvelle-example.com.au</div>
</section>

<section class="item envelope envelope--back-white" aria-label="DL envelope back, white">
  <svg class="flap" viewBox="0 0 374 70" preserveAspectRatio="none" aria-hidden="true">
    <path d="M0 0 L374 0 L374 22 C300 34 230 62 187 66 C144 62 74 34 0 22 Z" fill="var(--red)"/>
  </svg>
  <div class="logo flap-logo"><span class="logo__dot"></span></div>
  <div class="web">www.brandvelle-example.com.au</div>
</section>

<section class="item envelope envelope--back-red" aria-label="DL envelope back, red">
  <svg class="flap" viewBox="0 0 374 70" preserveAspectRatio="none" aria-hidden="true">
    <path d="M0 22 C74 34 144 62 187 66 C230 62 300 34 374 22" fill="none" stroke="#5e090c" stroke-width="1.5"/>
  </svg>
  <div class="logo flap-logo"><span class="logo__dot"></span><span class="logo__name">Brandvelle</span></div>
  <div class="web">www.brandvelle-example.com.au</div>
</section>

</body>
</html>
```